Veranix - Solution provider in business consulting

Veranix is a swiss based company providing solutions for developing markets. The business covers various fields of business consulting, such as supply chain, product costs, quality management and manufacturing management. The Business operates in a efficient, straight and solution oriented manner.
The final design should communicate these characteristics. Asian people as well as as western people shall identify the qualities of the company at first sight.
The customer needs business cards with a simple view but an recognizable design, printed in high quality. Engraved elements such as the globe or simple words are possible.
Available colors are: (RAL)
102/102/102
51/102/102
153/204/153
255/102/51
Font: Calibri

```html
<!DOCTYPE html>
<html lang="en">
<head>
<meta charset="utf-8">
<title>Veranix – Business Card</title>
<link href="https://fonts.googleapis.com/css2?family=Carlito:wght@400;700&display=swap" rel="stylesheet">
<style>
  :root {
    --page-bg: #e4e2de;
    --card-white: #ffffff;
    --card-white-shade: #ededed;
    --ral-grey: #666666;
    --grey-dark: #555555;
    --grey-light: #727272;
    --text-light: #f2f2f2;
    --text-muted: #9a9a9a;
    --mark-light: #d6d6d6;
    --stripe-hi: rgba(255,255,255,0.16);
    --stripe-lo: rgba(0,0,0,0.12);
  }
  * { box-sizing: border-box; margin: 0; padding: 0; }
  html, body {
    width: 1200px; height: 950px; overflow: hidden;
    background: var(--page-bg);
    font-family: "Carlito", "Calibri", sans-serif;
  }
  .sheet { position: relative; width: 1200px; height: 950px; }

  .card {
    position: absolute; left: 230px;
    width: 740px; height: 423px;
    overflow: hidden;
    box-shadow: 0 10px 28px rgba(0,0,0,0.22);
  }
  .card--front { top: 40px; background: var(--ral-grey); }
  .card--back  { top: 487px; background: linear-gradient(120deg, var(--grey-dark), var(--grey-light) 60%, var(--grey-dark)); }

  /* front */
  .front-top {
    position: absolute; left: 0; top: 0; width: 100%; height: 222px;
    background: linear-gradient(160deg, var(--card-white) 40%, var(--card-white-shade));
  }
  .brand {
    position: absolute; left: 56px; top: 26px;
    display: flex; align-items: center; gap: 14px;
  }
  .brand__name {
    font-size: 70px; font-weight: 400; color: var(--ral-grey);
    letter-spacing: 1px; line-height: 1;
  }
  .brand__dot { width: 22px; height: 22px; border-radius: 50%; background: var(--ral-grey); }
  .holder { position: absolute; left: 60px; top: 130px; }
  .holder__name { font-size: 26px; font-weight: 700; color: var(--ral-grey); }
  .holder__role { font-size: 16px; color: var(--text-muted); margin-top: 2px; }

  .contact {
    position: absolute; left: 52px; top: 246px; list-style: none;
    color: var(--text-light); font-size: 20px;
  }
  .contact li { display: flex; align-items: center; gap: 12px; height: 27px; }
  .contact svg { width: 18px; height: 18px; flex: none; fill: var(--text-light); }

  .company {
    position: absolute; left: 462px; top: 306px;
    color: var(--text-light); font-size: 19px; line-height: 1.3;
  }
  .company__name { font-weight: 700; }

  .engraved-band {
    position: absolute; top: 0; height: 100%; width: 42px;
    background: linear-gradient(90deg, transparent, var(--stripe-hi) 30%, var(--stripe-lo) 55%, var(--stripe-hi) 75%, transparent);
  }
  .card--front .engraved-band { left: 520px; }
  .card--back .engraved-band  { left: 500px; }

  /* back */
  .back-mark {
    position: absolute; left: 240px; top: 70px;
    width: 190px; height: 190px; border-radius: 50%;
    background: var(--mark-light);
  }
  .back-url {
    position: absolute; left: 270px; top: 286px;
    font-size: 28px; color: #a8a8a8; letter-spacing: 2px;
  }
</style>
</head>
<body>
<main class="sheet">

  <section class="card card--front" aria-label="Business card front">
    <div class="front-top"></div>
    <div class="engraved-band" role="img" aria-label="Engraved textured vertical band"></div>

    <div class="brand">
      <span class="brand__name">veranix</span>
      <span class="brand__dot"></span>
    </div>

    <div class="holder">
      <p class="holder__name">Marco Feller</p>
      <p class="holder__role">CEO</p>
    </div>

    <ul class="contact">
      <li>
        <svg viewBox="0 0 24 24" aria-hidden="true"><path d="M3 8c0-2 3-4 9-4s9 2 9 4v2h-5V8H8v2H3z"/><rect x="5" y="11" width="14" height="9" rx="2"/></svg>
        +41 71 830 4172
      </li>
      <li>
        <svg viewBox="0 0 24 24" aria-hidden="true"><path d="M7 2h10a1 1 0 0 1 1 1v18a1 1 0 0 1-1 1H7a1 1 0 0 1-1-1V3a1 1 0 0 1 1-1zm1 3v12h8V5z"/></svg>
        +41 79 526 3809
      </li>
      <li>
        <svg viewBox="0 0 24 24" aria-hidden="true"><path d="M2 5h20v14H2zm2 2v.5l8 5.5 8-5.5V7z"/></svg>
        marco.feller@veranix.ch
      </li>
      <li>
        <svg viewBox="0 0 24 24" aria-hidden="true"><circle cx="12" cy="12" r="10"/><path d="M2 12h20M12 2c3 3 3 17 0 20M12 2c-3 3-3 17 0 20" stroke="#666" stroke-width="1.5" fill="none"/></svg>
        www.veranix.ch
      </li>
    </ul>

    <address class="company" style="font-style:normal">
      <p class="company__name">Veranix GmbH</p>
      <p>Talstrasse 18, 9203 Neudorf</p>
      <p>Switzerland</p>
    </address>
  </section>

  <section class="card card--back" aria-label="Business card back">
    <div class="engraved-band" role="img" aria-label="Engraved textured vertical band"></div>
    <div class="back-mark"></div>
    <p class="back-url">veranix.ch</p>
  </section>

</main>
</body>
</html>
```